New business card/stationary for a consulting company

I am looking for a clean and very professional looking business card for my consulting company as well as corresponding stationary. I am uploading our logo. I like simple and powerful for the feel. No graphics but I am open on everything else. Below is my contact information but would like the final to be in a version I can add my employees information into and print. Thank you.

Daniel Whitcombe
dan@ferncliffadvisory.com
2870 North 9th Avenue, Summit Floor, Elm Ridge, Illinois 60531
www.ferncliffadvisory.com

Industry/Entity Type

Consulting

Contact Information for Business Card

Daniel Whitcombe
dan@ferncliffadvisory.com
www.ferncliffadvisory.com

Font styles to use
Serif
Sans Serif

Requirements
Must have
• Our logo and the business card details.
Nice to have
• our website www.ferncliffadvisory.com

```html
<!DOCTYPE html>
<html lang="en">
<head>
<meta charset="utf-8">
<title>Ferncliff Advisory — Business Card</title>
<link rel="stylesheet" href="https://fonts.googleapis.com/css2?family=Cinzel:wght@400&family=Montserrat:wght@400;600;800&display=swap">
<style>
  :root {
    --navy: #0a0a80;
    --ink: #1c1c2a;
    --paper: #ffffff;
    --backdrop: #e9e9ec;
  }
  * { margin: 0; padding: 0; box-sizing: border-box; }
  html, body {
    width: 1200px; height: 900px; overflow: hidden;
    background: var(--backdrop);
  }
  .card {
    position: absolute; left: 75px; top: 150px;
    width: 1050px; height: 600px;
    background: var(--paper);
    font-family: "Montserrat", sans-serif;
    color: var(--ink);
    overflow: hidden;
  }
  .brand-mark {
    position: absolute; left: 440px; top: 48px;
    width: 120px; height: 86px;
    background: var(--navy);
  }
  .brand-name {
    position: absolute; left: 150px; top: 150px;
    font-family: "Cinzel", serif; font-weight: 400;
    font-size: 46px; letter-spacing: 3px;
    color: var(--navy); white-space: nowrap;
  }
  .divider {
    position: absolute; left: 150px; top: 235px;
    width: 700px; height: 3px; background: var(--navy);
  }
  .contact-list {
    position: absolute; left: 110px; top: 270px;
    list-style: none;
  }
  .contact-list li {
    display: flex; align-items: center; gap: 20px;
    height: 50px; font-size: 26px; font-weight: 400;
    color: #3a3a48; letter-spacing: 0.5px;
  }
  .contact-list svg { width: 24px; height: 24px; fill: var(--navy); flex: none; }
  .person {
    position: absolute; right: 60px; top: 262px; text-align: right;
    color: var(--navy);
  }
  .person-name { font-size: 44px; font-weight: 800; letter-spacing: 0.5px; }
  .person-title { font-size: 26px; font-weight: 600; margin-top: 4px; }
  .address {
    position: absolute; right: 60px; top: 440px; text-align: right;
    font-size: 24px; line-height: 44px; color: var(--ink);
  }
  .footer-band {
    position: absolute; left: 0; bottom: 0;
    width: 100%; height: 40px; background: var(--navy);
  }
</style>
</head>
<body>
  <div class="card">
    <div class="brand-mark"></div>
    <div class="brand-name">FERNCLIFF ADVISORY</div>
    <div class="divider"></div>

    <ul class="contact-list">
      <li>
        <svg viewBox="0 0 24 24" aria-hidden="true"><path d="M6.6 10.8a15 15 0 0 0 6.6 6.6l2.2-2.2a1 1 0 0 1 1-.25 11.4 11.4 0 0 0 3.6.57 1 1 0 0 1 1 1V20a1 1 0 0 1-1 1A17 17 0 0 1 3 4a1 1 0 0 1 1-1h3.5a1 1 0 0 1 1 1c0 1.25.2 2.45.57 3.57a1 1 0 0 1-.25 1z"/></svg>
        (855) 302 71846
      </li>
      <li>
        <svg viewBox="0 0 24 24" aria-hidden="true"><path d="M7 2h10a2 2 0 0 1 2 2v16a2 2 0 0 1-2 2H7a2 2 0 0 1-2-2V4a2 2 0 0 1 2-2zm0 3v13h10V5zm5 14.2a1 1 0 1 0 0 .1z"/></svg>
        + 917730215846
      </li>
      <li>
        <svg viewBox="0 0 24 24" aria-hidden="true"><path d="M2 5h20v14H2zm2 2v.4l8 5 8-5V7l-8 5z"/></svg>
        dan@ferncliffadvisory.com
      </li>
      <li>
        <svg viewBox="0 0 24 24" aria-hidden="true"><path d="M12 2a10 10 0 1 0 0 20 10 10 0 0 0 0-20zm-1 2.1V8H7.6A8 8 0 0 1 11 4.1zm2 0A8 8 0 0 1 16.4 8H13zM6.5 10H11v4H6.5a8 8 0 0 1 0-4zm6.5 0h4.5a8 8 0 0 1 0 4H13zm-5.4 6H11v3.9A8 8 0 0 1 7.6 16zm5.4 0h3.4a8 8 0 0 1-3.4 3.9z"/></svg>
        www.ferncliffadvisory.com
      </li>
    </ul>

    <div class="person">
      <div class="person-name">Daniel Whitcombe</div>
      <div class="person-title">Founder / Principal</div>
    </div>

    <div class="address">
      2870 North 9th Avenue, Summit Floor,<br>
      Elm Ridge, Illinois 60531
    </div>

    <div class="footer-band"></div>
  </div>
</body>
</html>
```